Complete Stationary Package for Bird's Nest Exporting Company
Silver Crane Swiftlet House 银鹤燕屋
Complete Stationary Package for Bird's Nest Exporting Company - Food
Creative Brief
Simple
Malcolm Pryce 马康
Director of Sales and Distribution
Silver Crane Swiftlet House, Level 17, KL Plaza 5, Jalan Bukit Merah, Sentral, 50320 Kuala Lumpur, Malaysia
mpryce@scswiftlet.example
www.scswiftlet.example
We need a full stationary package design - business cards, letterhead, envelopes, folders, invoice, email signature and any other standard stationary items you may decide to include in your concepts. I need the text below written in smaller print somewhere on the card either on the front or the back " Silver Crane Swiftlet House is a registered trademark of Ridgemoor Holdings Sdn Bhd 2207815K". I like the same cream colour that is used in the packaging that I have uploaded. I do not want the card to have a white background colour. I would like red and/or gold to feature also.
I would like a suitable design for the back of the card with the company name and logo.

```html
<!DOCTYPE html>
<html lang="en">
<head>
<meta charset="utf-8">
<title>Silver Crane Swiftlet House — Business Card</title>
<link rel="stylesheet" href="https://fonts.googleapis.com/css2?family=Noto+Serif+SC:wght@500&family=Cormorant+Garamond:wght@500;600;700&display=swap">
<style>
  :root{
    --stage:#4f4840;
    --red:#c8141c;
    --red-deep:#a80f16;
    --red-emboss:#b5111a;
    --cream:#f3ecd9;
    --gold:#c39a2e;
    --ink:#8a6a22;
    --band-text:#f6e9c8;
  }
  *{margin:0;padding:0;box-sizing:border-box}
  html,body{width:1200px;height:904px;overflow:hidden;background:var(--stage)}
  .canvas{position:relative;width:1200px;height:904px;display:flex;justify-content:center;align-items:center;gap:80px}
  .card{position:relative;width:340px;height:580px;border-radius:170px 170px 6px 6px;overflow:hidden;box-shadow:0 6px 18px rgba(0,0,0,.35)}
  /* back of card */
  .card--back{background:var(--red)}
  .emboss-mark{position:absolute;left:50%;top:48px;width:230px;height:230px;margin-left:-115px;border-radius:50%;
    background:radial-gradient(circle at 45% 40%,#cf1820,var(--red-emboss));box-shadow:inset 2px 2px 3px rgba(0,0,0,.25),inset -2px -2px 3px rgba(255,255,255,.12)}
  .brand{font-family:"Noto Serif SC",serif;font-weight:500;text-align:center;letter-spacing:.08em}
  .card--back .brand{position:absolute;left:0;right:0;top:330px;color:var(--band-text)}
  .brand__cn{font-size:40px;line-height:1.2}
  .brand__en{font-size:15px;line-height:1.5;text-transform:uppercase;letter-spacing:.16em}
  /* front of card */
  .card--front{background:var(--cream)}
  .logo{position:absolute;left:0;right:0;top:52px;display:flex;flex-direction:column;align-items:center;gap:14px}
  .logo__dot{width:110px;height:110px;border-radius:50%;background:var(--gold)}
  .card--front .brand{color:var(--gold)}
  .card--front .brand__cn{font-size:32px}
  .card--front .brand__en{font-size:12px}
  .contact{position:absolute;left:40px;right:40px;top:300px;font-family:"Cormorant Garamond",serif;color:var(--ink)}
  .contact__name{font-size:22px;font-weight:700;color:var(--red)}
  .contact__name span{font-family:"Noto Serif SC",serif;font-size:17px;font-weight:500;margin-left:6px}
  .contact__title{font-size:14px;font-weight:600;margin-bottom:10px}
  .contact__address{font-size:13.5px;line-height:1.35;font-weight:500;margin-bottom:10px}
  .contact__row{display:flex;align-items:center;gap:8px;font-size:13.5px;font-weight:600;line-height:1.6}
  .contact__row svg{width:12px;height:12px;flex:none}
  .band{position:absolute;left:0;right:0;bottom:0;height:34px;background:var(--red);display:flex;align-items:center;justify-content:center;
    font-family:"Cormorant Garamond",serif;font-size:10.5px;font-weight:600;color:var(--band-text);letter-spacing:.02em;padding:0 12px;text-align:center}
</style>
</head>
<body>
<main class="canvas">
  <section class="card card--back" aria-label="Card back">
    <div class="emboss-mark"></div>
    <div class="brand">
      <div class="brand__cn">银鹤燕屋</div>
      <div class="brand__en">Silver Crane Swiftlet House</div>
    </div>
  </section>

  <section class="card card--front" aria-label="Card front">
    <div class="logo">
      <div class="logo__dot"></div>
      <div class="brand">
        <div class="brand__cn">银鹤燕屋</div>
        <div class="brand__en">Silver Crane Swiftlet House</div>
      </div>
    </div>
    <div class="contact">
      <div class="contact__name">Malcolm Pryce<span>马康</span></div>
      <div class="contact__title">Director of Sales and Distribution</div>
      <div class="contact__address">Silver Crane Swiftlet House<br>Level 17, KL Plaza 5<br>Jalan Bukit Merah, Sentral, 50320<br>Kuala Lumpur, Malaysia</div>
      <div class="contact__row"><svg viewBox="0 0 12 12"><circle cx="6" cy="6" r="6" fill="#c8141c"/><path d="M4 3.2l1 1.4-.6.7c.5 1 1.2 1.7 2.2 2.2l.7-.6 1.4 1-.5 1c-2.6-.4-4.4-2.2-4.8-4.8z" fill="#f3ecd9"/></svg>+60 3-2711 4820</div>
      <div class="contact__row"><svg viewBox="0 0 12 12"><circle cx="6" cy="6" r="6" fill="#c8141c"/><rect x="3" y="4" width="6" height="4" fill="none" stroke="#f3ecd9" stroke-width=".8"/><path d="M3 4l3 2.2L9 4" fill="none" stroke="#f3ecd9" stroke-width=".8"/></svg>+60 12-663 1907</div>
      <div class="contact__row"><svg viewBox="0 0 12 12"><circle cx="6" cy="6" r="6" fill="#c8141c"/><rect x="3" y="4" width="6" height="4" fill="none" stroke="#f3ecd9" stroke-width=".8"/><path d="M3 4l3 2.2L9 4" fill="none" stroke="#f3ecd9" stroke-width=".8"/></svg>mpryce@scswiftlet.example</div>
      <div class="contact__row"><svg viewBox="0 0 12 12"><circle cx="6" cy="6" r="6" fill="#c8141c"/><circle cx="6" cy="6" r="3" fill="none" stroke="#f3ecd9" stroke-width=".8"/><path d="M3 6h6M6 3c-1.2 1.6-1.2 4.4 0 6M6 3c1.2 1.6 1.2 4.4 0 6" fill="none" stroke="#f3ecd9" stroke-width=".6"/></svg>www.scswiftlet.example</div>
    </div>
    <div class="band">Silver Crane Swiftlet House is a registered trademark of Ridgemoor Holdings Sdn Bhd 2207815K</div>
  </section>
</main>
</body>
</html>
```